RTavenor Business Cards & Letterhead

I have a logo but need a design for some new business cards. We are a Design-Build Firm that specializes in the design and construction of commercial projects.
the cards need to be professional. no cartoon stuff.
i would like to have the cards in AI format so I can update the card as needed. Logo is provided.
Our Address is: 4187 Marlowe Ct. Apex, North Carolina 27614

```html
<!DOCTYPE html>
<html lang="en">
<head>
<meta charset="utf-8">
<title>RTavenor Business Card</title>
<link href="https://fonts.googleapis.com/css2?family=Arimo:wght@400;700&display=swap" rel="stylesheet">
<style>
:root{
  --backdrop:#2b2b2d;
  --brand-blue:#0a68a8;
  --brand-blue-dark:#064d80;
  --ink:#3a3a3c;
  --ink-soft:#6a6a6c;
  --paper:#f4f4f5;
  --strip:#3d3d40;
}
*{margin:0;padding:0;box-sizing:border-box}
html,body{width:1200px;height:947px;overflow:hidden}
body{background:var(--backdrop);font-family:"Arimo",Arial,sans-serif;position:relative}
.card{position:absolute;width:560px;height:320px;border-radius:22px;overflow:hidden}
.card-back{left:40px;top:130px;background:radial-gradient(ellipse at 55% 40%,#1683c6 0%,var(--brand-blue) 45%,var(--brand-blue-dark) 100%)}
.card-back .wordmark{position:absolute;left:0;right:0;top:132px;text-align:center;color:#fff;font-weight:700;font-size:50px;letter-spacing:1px}
.card-front{left:600px;top:500px;background:var(--paper)}
.edge-strip{position:absolute;left:0;top:0;bottom:0;width:18px;background:var(--strip)}
.edge-strip .accent{position:absolute;left:0;top:52px;width:18px;height:40px;background:var(--brand-blue)}
.front-logo{position:absolute;right:30px;top:34px;display:flex;align-items:center;gap:10px}
.front-logo .mark{width:22px;height:22px;background:var(--brand-blue)}
.front-logo .wordmark{color:var(--ink);font-weight:700;font-size:30px;letter-spacing:.5px}
.person{position:absolute;left:44px;top:56px}
.person .name{color:var(--brand-blue);font-weight:700;font-size:26px}
.person .role{color:var(--ink-soft);font-size:13px;margin-top:3px}
.address{position:absolute;left:44px;top:180px;color:var(--ink);font-size:15px;line-height:19px}
.contacts{position:absolute;left:44px;top:228px;list-style:none;color:var(--ink);font-size:15px;line-height:20px}
.contacts li{display:flex;align-items:center;gap:8px}
.contacts svg{width:13px;height:13px;fill:var(--brand-blue)}
</style>
</head>
<body>
<section class="card card-back">
  <div class="wordmark">RTAVENOR</div>
</section>

<section class="card card-front">
  <div class="edge-strip"><div class="accent"></div></div>
  <div class="front-logo"><span class="mark"></span><span class="wordmark">RTAVENOR</span></div>
  <div class="person">
    <div class="name">Dana Whitfield</div>
    <div class="role">Managing Director</div>
  </div>
  <div class="address">4187 Marlowe Ct. Apex<br>North Carolina 27614</div>
  <ul class="contacts">
    <li><svg viewBox="0 0 16 16"><path d="M3 1l3 3-1.5 2a9 9 0 005.5 5.5L12 10l3 3-2 2C7 15 1 9 1 3z"/></svg>919-555-0142</li>
    <li><svg viewBox="0 0 16 16"><path d="M4 0h8a1 1 0 011 1v14a1 1 0 01-1 1H4a1 1 0 01-1-1V1a1 1 0 011-1zm1 2v10h6V2z"/></svg>919-555-0178</li>
    <li><svg viewBox="0 0 16 16"><path d="M0 3h16v10H0zm1 1v.5l7 5 7-5V4z"/></svg>info@rtavenor.com</li>
    <li><svg viewBox="0 0 16 16"><circle cx="8" cy="8" r="7.5"/></svg>www.rtavenor.com</li>
  </ul>
</section>
</body>
</html>
```